Natural Light/Organic/Documentary Photography Business

I like a simple, approachable, feminine, earthy/organic feel. Earth/neutral tones, nothing too loud or obnoxious. I like the watercolor look. I don't want anything too trendy or something I'll get tired of after a couple months. As far as colors, I am much more a fan of cream/taupe/blue/green...not a fan of pink or purple at all.

Target Market(s)

Weddings & Families

Industry/Entity Type

Wedding Photography

Contact Information for Business Card

website, email, phone number

Font styles to use
Other font styles liked:
• Horizontes, Gotham

Colors

Designer to choose colors to be used in the design.

Requirements
Must have
• Website: www.mirelhatchway.com
• Phone: 418.629.5073
• Email: mirel@mirelhatchway.com
Nice to have
• I like the watercolor look but its not necessary. I like simple/earthy tones. Nothing too loud or distracting. Simple & feminine without being too girly. I like an approachable/soft feel.
• Instagram: www.snapfolio.net/mirelhatchwayphotography/
Should not have
• NO loud colors or design or pattern. I do not want a photo of a camera or lens or anything cheesy like that.

```html
<!DOCTYPE html>
<html lang="en">
<head>
<meta charset="utf-8">
<title>Mirel Hatchway Photography — Business Card</title>
<link href="https://fonts.googleapis.com/css2?family=Open+Sans:wght@400&display=swap" rel="stylesheet">
<style>
  :root {
    --backdrop: #3b322d;
    --card: #0d0d0d;
    --ink-soft: #a9a29c;
    --ink-muted: #6f6a66;
    --ink-bright: #e9e6e2;
    --rule: #5a5652;
  }
  * { margin: 0; padding: 0; box-sizing: border-box; }
  html, body {
    width: 1200px;
    height: 844px;
    overflow: hidden;
    background: var(--backdrop);
    font-family: "Open Sans", Arial, sans-serif;
  }
  .stage {
    width: 1200px;
    height: 844px;
    display: flex;
    align-items: center;
    justify-content: center;
    gap: 50px;
  }
  .card {
    width: 525px;
    height: 300px;
    background: var(--card);
    position: relative;
    display: flex;
    flex-direction: column;
    align-items: center;
    box-shadow: 0 6px 18px rgba(0,0,0,0.35);
  }
  .brand-name {
    font-size: 26px;
    font-weight: 400;
    letter-spacing: 1px;
    white-space: nowrap;
  }
  .card-front { padding-top: 82px; }
  .card-front .brand-name { color: var(--ink-soft); }
  .contact-list {
    list-style: none;
    margin-top: 48px;
    text-align: center;
    font-size: 15px;
    line-height: 21px;
    color: var(--ink-soft);
  }
  .contact-list .label { color: var(--ink-muted); }
  .card-back { padding-top: 70px; }
  .card-back .brand-name { color: var(--ink-bright); }
  .divider {
    width: 390px;
    height: 14px;
    margin-top: 32px;
  }
  .divider svg { display: block; }
  .social-url {
    margin-top: 26px;
    font-size: 15px;
    color: var(--ink-bright);
    white-space: nowrap;
  }
</style>
</head>
<body>
<main class="stage">
  <section class="card card-front" aria-label="Card front">
    <p class="brand-name">Mirel Hatchway Photography</p>
    <ul class="contact-list">
      <li><span class="label">P:</span> 418.629.5073</li>
      <li><span class="label">E:</span> mirel@mirelhatchway.com</li>
      <li><span class="label">W:</span> www.mirelhatchway.com</li>
    </ul>
  </section>

  <section class="card card-back" aria-label="Card back">
    <p class="brand-name">Mirel Hatchway Photography</p>
    <div class="divider">
      <svg width="390" height="14" viewBox="0 0 390 14" aria-hidden="true">
        <line x1="0" y1="7" x2="183" y2="7" stroke="var(--rule)" stroke-width="1"/>
        <line x1="207" y1="7" x2="390" y2="7" stroke="var(--rule)" stroke-width="1"/>
        <circle cx="195" cy="7" r="7" fill="var(--ink-bright)"/>
      </svg>
    </div>
    <p class="social-url">www.snapfolio.net/mirelhatchwayphotography/</p>
  </section>
</main>
</body>
</html>
```